Supplement Brand Product Labels

Product Label for Supplement Brand

Protein Powder Label (2 x different flavours)

Neon Colours / Skull / Spooky
Refer to pictures below, they are the look we are wanting to go with but put our touch to it aswell.

Target Market(s)

Fitness

Industry/Entity Type

Supplement Brand

Colors
0054AA
0677BA
7BADD7
CADEEF
E8F1F8
0094D4
00A9DD
6FCCEA
C7EBF8
E9F6FB
00AB8E
00BBA5
67D7C9
C6EFE9
E9F9F6
59FF00
82FF00
B8FF75
E3FFCB
F4FFEA
FFF300
FFF600
FEFA6F
FFFEC7
FFFEE8
FFC000
F8CF3A
FAE287
FDF2CF
FEFAEE
F0912C
F2A743
F7CA91
FBE8D2
FDF5EE
EE7325
F08F49
F5BC92
FAE3D3
FDF4ED
EB3D1F
EC4F4E
F09395
F8D3D4
FCEDEE
E54698
E96AAD
F1A4CE
F9D9EA
FCEFF6
A7469A
B969AE
D3A5CF
EDDBEB
F8F0F9
6B429C
8869AF
B7A5CE
E3DAEB
F3F0F8

Requirements
Nice to have
• Skull, Neon Colours, Abstract, Barbell, Lighting Bolt, Flames, Spooky

```html
<!DOCTYPE html>
<html lang="en">
<head>
<meta charset="utf-8">
<title>Voltrax Labs – BCAA 2:1:1 Label</title>
<link href="https://fonts.googleapis.com/css2?family=Lato:wght@400;700;900&family=Roboto+Slab:wght@700&family=Orbitron:wght@900&display=swap" rel="stylesheet">
<style>
  :root {
    --ink-dark: #0c0716;
    --ink-deep: #1a0d2e;
    --violet: #6b429c;
    --magenta: #e54698;
    --pink-soft: #b969ae;
    --blue-smoke: #3a3aa8;
    --lime: #59ff00;
    --amber: #ffc000;
    --text-light: #ffffff;
  }
  * { margin: 0; padding: 0; box-sizing: border-box; }
  html, body { width: 1200px; height: 548px; overflow: hidden; background: var(--ink-dark); }
  .label {
    position: relative;
    width: 1200px;
    height: 548px;
    overflow: hidden;
    color: var(--text-light);
    font-family: "Lato", sans-serif;
    background:
      radial-gradient(ellipse 420px 300px at 590px 180px, rgba(107,66,156,0.55), transparent 70%),
      radial-gradient(ellipse 300px 260px at 820px 120px, rgba(58,58,168,0.35), transparent 70%),
      radial-gradient(ellipse 260px 240px at 360px 160px, rgba(58,58,168,0.3), transparent 70%),
      linear-gradient(180deg, var(--ink-dark) 0%, var(--ink-deep) 60%, #221040 100%);
  }
  .hero-art {
    position: absolute;
    left: 405px;
    top: 40px;
    width: 370px;
    height: 508px;
    border-radius: 46% 46% 30% 30% / 40% 40% 20% 20%;
    background:
      radial-gradient(ellipse at 50% 18%, rgba(229,70,152,0.95) 0%, rgba(185,105,174,0.7) 35%, transparent 70%),
      radial-gradient(ellipse at 50% 88%, rgba(89,255,0,0.35) 0%, rgba(255,192,0,0.25) 30%, transparent 60%),
      linear-gradient(180deg, #8a2f8e 0%, #3d2470 55%, #2a1a3e 100%);
    opacity: 0.9;
    filter: blur(2px);
  }
  .directions {
    position: absolute;
    left: 28px;
    top: 48px;
    width: 298px;
  }
  .section-title {
    font-family: "Roboto Slab", serif;
    font-weight: 700;
    font-size: 15.5px;
    line-height: 20px;
  }
  .directions .dosage {
    margin-top: 12px;
    font-size: 11.6px;
    line-height: 16.6px;
  }
  .directions .advisory {
    margin-top: 21px;
    font-size: 11.6px;
    line-height: 16.6px;
    text-align: justify;
    text-align-last: justify;
  }
  .directions .storage {
    margin-top: 20px;
    font-size: 11.6px;
    font-weight: 700;
  }
  .brand-name {
    position: absolute;
    font-family: "Lato", sans-serif;
    font-weight: 900;
    color: var(--text-light);
    letter-spacing: 1px;
    display: flex;
    align-items: center;
    gap: 6px;
  }
  .brand-name .mark {
    width: 12px;
    height: 12px;
    background: var(--lime);
  }
  .brand-name.front { left: 528px; top: 140px; font-size: 26px; }
  .brand-name.footer { left: 60px; top: 444px; font-size: 26px; }
  .product-title {
    position: absolute;
    left: 446px;
    top: 312px;
    width: 306px;
    text-align: center;
    font-family: "Orbitron", sans-serif;
    font-weight: 900;
    font-size: 45px;
    line-height: 50px;
    letter-spacing: 2px;
  }
  .nutrition {
    position: absolute;
    left: 872px;
    top: 50px;
    width: 300px;
    height: 262px;
    border: 2px solid var(--text-light);
  }
  .nutrition table {
    width: 100%;
    border-collapse: collapse;
  }
  .nutrition thead th {
    font-size: 9.5px;
    font-weight: 700;
    line-height: 12px;
    padding: 6px 0 6px;
    border-bottom: 2px solid var(--text-light);
    vertical-align: bottom;
  }
  .nutrition thead th.serves { text-align: left; padding-left: 8px; }
  .nutrition tbody td {
    font-size: 11px;
    height: 29.7px;
  }
  .nutrition tbody tr:first-child td { padding-top: 4px; }
  .nutrition td.nutrient { padding-left: 8px; width: 130px; }
  .nutrition td.per-serve { text-align: center; width: 58px; padding-right: 8px; }
  .nutrition td.per-100 { text-align: right; padding-right: 36px; }
  .ingredients {
    position: absolute;
    left: 882px;
    top: 334px;
  }
  .ingredients p {
    margin-top: 8px;
    font-size: 11.6px;
  }
  .origin {
    position: absolute;
    left: 951px;
    top: 480px;
    display: flex;
    align-items: center;
    gap: 4px;
  }
  .origin .map-art {
    width: 34px;
    height: 30px;
    background: var(--text-light);
    border-radius: 40% 50% 45% 35%;
  }
  .origin .origin-text {
    font-family: "Orbitron", sans-serif;
    font-weight: 900;
    font-size: 14px;
    line-height: 16px;
    letter-spacing: 0.5px;
  }
</style>
</head>
<body>
<main class="label">
  <div class="hero-art" role="img" aria-label="Neon pink, purple and lime skull illustration wrapped in coloured smoke"></div>

  <section class="directions">
    <h2 class="section-title">Directions Of Use</h2>
    <p class="dosage">Mix 7g (1 scoop) with 250ml's of cold water/ juice.</p>
    <p class="advisory">Formulated supplementary sports food. Not suitable for children under 15 years of age or pregnant women. Should only be used under medical or dietetic supervision. This product is not a sole source of nutrition and should be consumed in conjunction with a nutritious diet and appropriate physical training or exercise</p>
    <p class="storage">Store in a cool dry place out of direct sunlight.</p>
  </section>

  <div class="brand-name front">VOLTRAX<span class="mark"></span></div>
  <h1 class="product-title">BCAA 2:1:1</h1>
  <div class="brand-name footer">VOLTRAX<span class="mark"></span></div>

  <section class="nutrition">
    <table>
      <thead>
        <tr>
          <th class="serves">35.7 Servings<br>Per 250g Packet<br>7 Grams Per Serve</th>
          <th>Average Quantity<br>Per Serving</th>
          <th>Average Quantity<br>Per 100g</th>
        </tr>
      </thead>
      <tbody>
        <tr><td class="nutrient">Energy (KJ)</td><td class="per-serve">119</td><td class="per-100">1700</td></tr>
        <tr><td class="nutrient">Protein (G)</td><td class="per-serve">7</td><td class="per-100">100</td></tr>
        <tr><td class="nutrient">Total Carbohydrates (G)</td><td class="per-serve">0</td><td class="per-100">0</td></tr>
        <tr><td class="nutrient">(Sugar) (G)</td><td class="per-serve">0</td><td class="per-100">0</td></tr>
        <tr><td class="nutrient">Total Fats (G)</td><td class="per-serve">0</td><td class="per-100">0</td></tr>
        <tr><td class="nutrient">Sodium (MG)</td><td class="per-serve">0</td><td class="per-100">0</td></tr>
        <tr><td class="nutrient">BCAA 2:1:1 (G)</td><td class="per-serve">7</td><td class="per-100">100</td></tr>
      </tbody>
    </table>
  </section>

  <section class="ingredients">
    <h2 class="section-title">Ingredients</h2>
    <p>Arginine Alpha-Ketoglutarate</p>
  </section>

  <div class="origin">
    <div class="map-art" role="img" aria-label="Outline map of Australia"></div>
    <div class="origin-text">MADE IN<br>AUSTRALIA</div>
  </div>
</main>
</body>
</html>
```